Business Cards for new orthopaedic surgery practice

My husband and I are starting our own orthopaedic surgery practice. We are looking for a business card that is uniform, but one will have my name/title and the other will have his. You can just create one design with my name on it for now. But when I choose your design as the winning design I will ask that you add another copy with his name/title.

We are looking for classy, simple, elite all in one. We like dark blues/a little gold/yellow. Something that goes with our logo. We want our logo incorporated. Here is all the info you need:
Business name: RV Bone & Vitality Center
Location: 38517 North Willowmere Ave
Brightwater Bay, FL 33908
Phone: 954-218-4063
Fax: 954-582-7341
Email: info@myrvbonecare.example

Names: Lydia Vance, M.D.
Board Certified Hand and Upper Extremity Surgeon

Ebo Dansu, M.D.
Board Certified Hip & Knee Replacement/General Orthopaedic Surgeon

Can decide what you want to put on the back. Maybe a slogan:
Steady Hands. Lasting Strength

I am just going to upload our logo. The only thing is if we select you as the winning design, the location, and phone numbers may change. We will need your help to update that once fully solidified.

Industry/Entity Type

Medical

Contact Information for Business Card

Colors
0054AA
0677BA
7BADD7
CADEEF
E8F1F8
0094D4
00A9DD
6FCCEA
C7EBF8
E9F6FB

Requirements
Must have
• class, appeal,
Should not have
• We want to air on the side of masculine if we are looking at masculine vs. feminine feel. But we still want it classy, sophisticated, and something we will love

```html
<!DOCTYPE html>
<html lang="en">
<head>
<meta charset="utf-8">
<title>RV Bone &amp; Vitality Center — Business Card</title>
<link rel="stylesheet" href="https://fonts.googleapis.com/css2?family=Montserrat:wght@400;500;700&display=swap">
<style>
  :root {
    --navy: #1b2a52;
    --gold: #c9a45e;
    --white: #ffffff;
    --stage: #3a3a3c;
  }
  * { box-sizing: border-box; margin: 0; padding: 0; }
  html, body {
    width: 1200px; height: 875px; overflow: hidden;
    background: var(--stage);
    font-family: "Montserrat", Arial, sans-serif;
  }
  .sheet {
    width: 1200px; height: 875px;
    display: flex; align-items: center; justify-content: center; gap: 40px;
  }
  .card {
    position: relative;
    width: 540px; height: 309px;
    background: var(--navy);
    border-radius: 18px;
    overflow: hidden;
    color: var(--white);
  }

  /* Back side */
  .brand-seal {
    position: absolute; left: 182px; top: 40px;
    width: 176px; height: 176px;
    border: 2px solid var(--gold); border-radius: 50%;
    display: flex; align-items: center; justify-content: center;
    text-align: center;
  }
  .brand-seal__name {
    font-weight: 700; font-size: 17px; line-height: 1.3;
    letter-spacing: 0.08em; text-transform: uppercase;
    color: var(--white);
  }
  .slogan {
    position: absolute; left: 0; right: 0; top: 246px;
    text-align: center; font-size: 17px; font-weight: 400;
    letter-spacing: 0.01em;
  }

  /* Front side */
  .front__seal {
    position: absolute; right: 26px; top: 22px;
    width: 104px; height: 104px;
    border: 1.5px solid var(--gold); border-radius: 50%;
    background: var(--navy);
    display: flex; align-items: center; justify-content: center; text-align: center;
    z-index: 2;
  }
  .front__seal-name {
    font-weight: 700; font-size: 10px; line-height: 1.35;
    letter-spacing: 0.08em; text-transform: uppercase; color: var(--white);
  }
  .name-band {
    position: absolute; left: 0; top: 62px;
    width: 430px; height: 56px;
    background: var(--gold);
    padding: 8px 0 0 36px;
    color: var(--navy);
  }
  .name-band__name {
    font-weight: 700; font-size: 18px; letter-spacing: 0.02em; text-transform: uppercase;
  }
  .name-band__title { font-size: 11.5px; font-weight: 500; margin-top: 2px; }

  .contact {
    position: absolute; left: 112px; top: 156px;
    font-size: 13px; line-height: 1.45;
  }
  .contact__address { margin-bottom: 14px; }
  .contact__list { list-style: none; }
  .contact__item { display: flex; align-items: center; gap: 8px; }
  .contact__icon { width: 11px; height: 11px; flex: none; fill: var(--gold); }
</style>
</head>
<body>
<main class="sheet">

  <section class="card card--back" aria-label="Card back">
    <div class="brand-seal">
      <span class="brand-seal__name">RV Bone &amp;<br>Vitality<br>Center</span>
    </div>
    <p class="slogan">Steady Hands. Lasting Strength</p>
  </section>

  <section class="card card--front" aria-label="Card front">
    <div class="name-band">
      <h1 class="name-band__name">Lydia Vance, M.D.</h1>
      <p class="name-band__title">Board Certified Hand and Upper Extremity Surgeon</p>
    </div>
    <div class="front__seal">
      <span class="front__seal-name">RV Bone &amp;<br>Vitality<br>Center</span>
    </div>

    <div class="contact">
      <p class="contact__address">38517 North Willowmere Ave<br>Brightwater Bay, FL 33908</p>
      <ul class="contact__list">
        <li class="contact__item">
          <svg class="contact__icon" viewBox="0 0 24 24" aria-hidden="true"><path d="M6.6 10.8a15 15 0 0 0 6.6 6.6l2.2-2.2a1 1 0 0 1 1-.25 11.4 11.4 0 0 0 3.6.57 1 1 0 0 1 1 1V20a1 1 0 0 1-1 1A17 17 0 0 1 3 4a1 1 0 0 1 1-1h3.5a1 1 0 0 1 1 1c0 1.25.2 2.450.57 3.57a1 1 0 0 1-.25 1z"/></svg>
          954-218-4063
        </li>
        <li class="contact__item">
          <svg class="contact__icon" viewBox="0 0 24 24" aria-hidden="true"><path d="M6 2h10v5H6zM3 8h18a1 1 0 0 1 1 1v8h-4v5H6v-5H2V9a1 1 0 0 1 1-1zm5 8v4h8v-4z"/></svg>
          954-582-7341
        </li>
        <li class="contact__item">
          <svg class="contact__icon" viewBox="0 0 24 24" aria-hidden="true"><path d="M2 5h20v14H2zm2 2v.5l8 5.5 8-5.5V7l-8 5.5z"/></svg>
          info@myrvbonecare.example
        </li>
      </ul>
    </div>
  </section>

</main>
</body>
</html>
```